Ledger Tide Folk Banner Ad campaign

We are the number 1 leading automated journal & analytics platform for active traders in the crypto space

We will be running banner ads on a specialist ad network and need HTML designs + a good strategy.

Some of our key selling points to consider including:

- The #1 automated journaling & analytics solution for Crypto Traders
- We save traders time (from manual data entry that can be automated by our journal trade import service)
- We help traders improve through detailed analytics feedback on their trading performance
- LTF has helped thousands of crypto traders improve performance
- 5,700+ traders are using LTF to save themselves hundreds of data entry hours per year
- Analyse your full trade history in a click!

I have attached an example mockup we came up with internally but we are not professionals. Use it as a guide to heavily improve upon in the context of general design quality, and 'sales-y' lingo to improve conversions
Updates

Have added a £100 1st place payment increase upon advice from a designer Should incentivise the best of the best to submit work

Target Market(s)

Active traders in the crypto derivatives space. Trading on the following exchanges:

- Zorvex.com
- Quillaro.com
- Tavomen.com
- KWP.com

Font styles to use
Other font styles liked:
• Quicksand is our main font atm

Colors
3277b5
33a6d7
0792cd
85abd2
3276b5
85acd3
85cae6
86cae7

Requirements
Must have
• similar colour scheme from my example upload.

Check our main website for more: ledgertidefolk.example

Although bare in mind, its a bit old and shitty. We are now working with specialists to improve, so feel free to have some creative freedom
Nice to have
• Nice clear custom icons to accompany text. And a rotation of 2 or 3 of the main selling points from the project description

```html
<!DOCTYPE html>
<html lang="en">
<head>
<meta charset="utf-8">
<title>Ledger Tide Folk – Banner Set</title>
<link rel="stylesheet" href="https://fonts.googleapis.com/css2?family=Quicksand:wght@400;500;700&display=swap">
<style>
  :root {
    --sheet: #cfcfcf;
    --teal: #3aa8cb;
    --blue: #2a5ea8;
    --yellow: #fcef50;
    --white: #ffffff;
    --ink: #111111;
    --body-ink: #1c1c1c;
  }
  * { box-sizing: border-box; margin: 0; padding: 0; }
  html, body { width: 1200px; height: 695px; overflow: hidden; }
  body {
    background: var(--sheet);
    font-family: "Quicksand", sans-serif;
    position: relative;
  }
  .banner {
    position: absolute;
    width: 360px;
    height: 301px;
    background: var(--yellow);
    overflow: hidden;
  }
  .banner--1 { left: 30px;  top: 33px; }
  .banner--2 { left: 420px; top: 33px; }
  .banner--3 { left: 810px; top: 33px; }
  .banner--4 { left: 30px;  top: 359px; }
  .banner--5 { left: 420px; top: 359px; }

  .banner__sky {
    position: absolute; left: 0; top: 0;
    width: 360px; height: 168px;
    background: linear-gradient(90deg, var(--teal), var(--blue));
  }
  .brand {
    position: absolute; left: 32px; top: 19px;
    display: flex; align-items: center; gap: 20px;
    color: var(--white);
  }
  .brand__mark {
    width: 24px; height: 24px;
    border: 2px solid var(--white);
    border-radius: 3px;
  }
  .brand__name {
    font-weight: 500;
    font-size: 22px;
    letter-spacing: 1.6px;
    line-height: 1;
  }
  .frame {
    position: absolute; left: 0; top: 0;
    width: 360px; height: 301px;
  }
  .card {
    position: absolute; left: 0; top: 73px;
    width: 323px; height: 137px;
    background: var(--white);
    border-radius: 0 10px 10px 0;
  }
  .banner--5 .card { width: 290px; }
  .card__art {
    position: absolute; left: 28px; top: 23px;
    width: 76px; height: 76px;
    border-radius: 6px;
    background: linear-gradient(135deg, #fdf37a, var(--yellow));
  }
  .card__copy {
    position: absolute; left: 115px; top: 22px;
    color: var(--body-ink);
  }
  .card__title {
    font-weight: 700;
    font-size: 17px;
    letter-spacing: 1.2px;
    line-height: 20px;
    color: var(--ink);
  }
  .card__body {
    font-weight: 500;
    font-size: 15px;
    letter-spacing: 0.6px;
    line-height: 20px;
  }
  .banner--2 .card__copy { left: 111px; }
  .banner--2 .card__body { font-size: 13px; line-height: 17.5px; letter-spacing: 0.4px; margin-top: 2px; }
  .banner--3 .card__copy { left: 112px; top: 14px; }
  .banner--3 .card__body { font-size: 14px; line-height: 18px; letter-spacing: 0.6px; margin-top: 1px; }
  .banner--4 .card__body { font-size: 14px; line-height: 18px; letter-spacing: 0.4px; margin-top: 2px; }
  .banner--5 .card__copy { left: 120px; top: 28px; }
  .banner--5 .card__body { font-size: 16px; line-height: 20px; letter-spacing: 0.8px; margin-top: 3px; }

  .cta {
    position: absolute; left: 28px; top: 190px;
    width: 103px; height: 37px;
    border-radius: 7px;
    background: linear-gradient(90deg, var(--teal), var(--blue));
    color: var(--white);
    font-weight: 700;
    font-size: 25px;
    letter-spacing: 1.5px;
    display: flex; align-items: center; justify-content: center;
    line-height: 1;
  }
  .offer {
    position: absolute; left: 29px; top: 234px;
    font-weight: 700;
    font-size: 26px;
    line-height: 24px;
    letter-spacing: 1.2px;
    background: linear-gradient(90deg, var(--teal), var(--blue) 70%);
    -webkit-background-clip: text;
    background-clip: text;
    color: transparent;
  }
</style>
</head>
<body>

<section class="banner banner--1">
  <div class="banner__sky"></div>
  <div class="brand"><span class="brand__mark"></span><span class="brand__name">LEDGER TIDE FOLK</span></div>
  <svg class="frame" viewBox="0 0 360 301"><path d="M199 168 V276 Q199 286 209 286 H333 Q343 286 343 276 V168" fill="none" stroke="#111" stroke-width="1.6"/></svg>
  <div class="card">
    <div class="card__art" role="img" aria-label="Yellow line icon of an analytics report with a rising chart and gear"></div>
    <div class="card__copy">
      <p class="card__title">THE #1 AUTOMATED</p>
      <p class="card__body">journaling &amp; analytics<br>solution for Crypto<br>Traders</p>
    </div>
  </div>
  <div class="cta">START</div>
  <p class="offer">YOUR FREE<br>TRIAL NOW</p>
</section>

<section class="banner banner--2">
  <div class="banner__sky"></div>
  <div class="brand"><span class="brand__mark"></span><span class="brand__name">LEDGER TIDE FOLK</span></div>
  <svg class="frame" viewBox="0 0 360 301"><path d="M199 168 V276 Q199 286 209 286 H333 Q343 286 343 276 V168" fill="none" stroke="#111" stroke-width="1.6"/></svg>
  <div class="card">
    <div class="card__art" role="img" aria-label="Yellow line icon of a stopwatch resting on an open hand"></div>
    <div class="card__copy">
      <p class="card__title">WE SAVE TRADERS TIME</p>
      <p class="card__body">(from manual data entry that<br>can be automated by our<br>journal trade import service)</p>
    </div>
  </div>
  <div class="cta">START</div>
  <p class="offer">YOUR FREE<br>TRIAL NOW</p>
</section>

<section class="banner banner--3">
  <div class="banner__sky"></div>
  <div class="brand"><span class="brand__mark"></span><span class="brand__name">LEDGER TIDE FOLK</span></div>
  <svg class="frame" viewBox="0 0 360 301"><path d="M199 168 V276 Q199 286 209 286 H333 Q343 286 343 276 V168" fill="none" stroke="#111" stroke-width="1.6"/></svg>
  <div class="card">
    <div class="card__art" role="img" aria-label="Yellow line icon of rising arrows above two gears"></div>
    <div class="card__copy">
      <p class="card__title">WE HELP<br>TRADERS IMPROVE</p>
      <p class="card__body">through detailed<br>analytics feedback on<br>their trading performance</p>
    </div>
  </div>
  <div class="cta">START</div>
  <p class="offer">YOUR FREE<br>TRIAL NOW</p>
</section>

<section class="banner banner--4">
  <div class="banner__sky"></div>
  <div class="brand"><span class="brand__mark"></span><span class="brand__name">LEDGER TIDE FOLK</span></div>
  <svg class="frame" viewBox="0 0 360 301"><path d="M199 168 V276 Q199 286 209 286 H333 Q343 286 343 276 V168" fill="none" stroke="#111" stroke-width="1.6"/></svg>
  <div class="card">
    <div class="card__art" role="img" aria-label="Yellow line icon of a trader at a desk surrounded by data screens"></div>
    <div class="card__copy">
      <p class="card__title">5,700+ TRADERS</p>
      <p class="card__body">are using LTF to save<br>themselves hundreds of<br>data entry hours per year</p>
    </div>
  </div>
  <div class="cta">START</div>
  <p class="offer">YOUR FREE<br>TRIAL NOW</p>
</section>

<section class="banner banner--5">
  <div class="banner__sky"></div>
  <div class="brand"><span class="brand__mark"></span><span class="brand__name">LEDGER TIDE FOLK</span></div>
  <svg class="frame" viewBox="0 0 360 301"><path d="M199 168 V276 Q199 286 209 286 H333 Q343 286 343 276 V168" fill="none" stroke="#111" stroke-width="1.6"/></svg>
  <div class="card">
    <div class="card__art" role="img" aria-label="Yellow line icon of a pie chart linked to data panels"></div>
    <div class="card__copy">
      <p class="card__title">ANALYSE YOUR</p>
      <p class="card__body">full trade history<br>in a click!</p>
    </div>
  </div>
  <div class="cta">START</div>
  <p class="offer">YOUR FREE<br>TRIAL NOW</p>
</section>

</body>
</html>
```